Local Flower Farm Needs Business Card Design

I need business cards designed for a flower farm based in Eudora, Kansas.
Business Info:
We are a local cut flower farm located in Eudora, Kansas, founded by Corinne Haldwick. What started as a passion for agriculture and search for more joy in daily life has blossomed into a small business dedicated to providing the community with beautiful, fresh, and sustainable flowers. We specialize in local, seasonal blooms, ensuring that every petal reflects the care and dedication we pour into our craft. Our mission is to deliver the highest quality flowers directly to our customers through local farmers markets and to florists who share our commitment to sustainability. Join us in celebrating the beauty of nature, one bloom at a time!
Contact Details:
Corinne Haldwick
Owner
Phone 913-555-0147
Facebook: Rosalind Thorpe Gardens
Instagram: @RosalindThorpeGardens
Website: RosalindThorpeGardens.example
Target Market(s)
Wholesale to Florists and Direct to Consumer via Farmers Market
Industry/Entity Type
Florist, Farm
Contact Information for Business Card
Name, Contact Info, Logo
Look and feel
Each slider illustrates characteristics of the customer's brand and the style your logo design should communicate.

```html
<!DOCTYPE html>
<html lang="en">
<head>
<meta charset="utf-8">
<title>Rosalind Thorpe Gardens – Business Card</title>
<link href="https://fonts.googleapis.com/css2?family=Tinos:wght@400;700&display=swap" rel="stylesheet">
<style>
  :root {
    --ink: #0b2830;
    --paper: #ffffff;
    --backdrop: #dfe3e5;
  }
  * { margin: 0; padding: 0; box-sizing: border-box; }
  html, body {
    width: 1200px;
    height: 960px;
    overflow: hidden;
    background: var(--backdrop);
    font-family: "Tinos", "Times New Roman", serif;
  }
  .card {
    position: absolute;
    width: 704px;
    height: 402px;
    overflow: hidden;
  }
  .card-front { left: 248px; top: 58px; background: var(--paper); }
  .card-back  { left: 248px; top: 500px; background: var(--ink); }

  .seal {
    position: absolute;
    border-radius: 50%;
    display: flex;
    align-items: center;
    justify-content: center;
    text-align: center;
    font-weight: 400;
    line-height: 1.15;
    letter-spacing: 0.06em;
    text-transform: uppercase;
  }
  .card-front .seal {
    left: 217px; top: 67px;
    width: 270px; height: 270px;
    border: 1px solid var(--ink);
    color: var(--ink);
    font-size: 30px;
  }
  .card-back .seal {
    left: 520px; top: 30px;
    width: 152px; height: 152px;
    border: 1px solid var(--paper);
    color: var(--paper);
    font-size: 17px;
  }

  .feature-panel {
    position: absolute;
    left: 0; top: 0;
    width: 340px; height: 402px;
  }
  .feature-name {
    position: absolute;
    left: 20px; top: 70px;
    color: var(--ink);
    font-size: 54px;
    font-weight: 400;
    line-height: 1.05;
    text-transform: uppercase;
    letter-spacing: 0.02em;
  }

  .identity {
    position: absolute;
    right: 30px; top: 218px;
    text-align: right;
    color: var(--paper);
  }
  .identity .person { font-size: 31px; font-weight: 700; letter-spacing: 0.02em; line-height: 1.1; }
  .identity .role { font-size: 18px; font-weight: 400; margin-top: 2px; }
  .accent-bar {
    position: absolute;
    right: 0; top: 224px;
    width: 14px; height: 46px;
    background: var(--paper);
  }

  .contacts {
    position: absolute;
    right: 28px; top: 296px;
    list-style: none;
    color: var(--paper);
    font-size: 17px;
    letter-spacing: 0.02em;
  }
  .contacts li {
    display: flex;
    justify-content: flex-end;
    align-items: center;
    height: 24px;
  }
  .contacts .icon {
    width: 16px; height: 16px;
    margin-left: 14px;
    flex: none;
  }
  .mark-circle { border-radius: 50%; background: var(--paper); }
  .mark-square { border-radius: 3px; border: 2px solid var(--paper); }
</style>
</head>
<body>

  <section class="card card-front">
    <div class="seal">Rosalind<br>Thorpe<br>Gardens</div>
  </section>

  <section class="card card-back">
    <svg class="feature-panel" viewBox="0 0 340 402" aria-hidden="true">
      <path d="M0 0 H340 V150 C330 260 300 330 210 402 H0 Z" fill="var(--paper)"/>
    </svg>
    <div class="feature-name">Rosalind<br>Thorpe<br>Gardens</div>

    <div class="seal">Rosalind<br>Thorpe<br>Gardens</div>

    <div class="identity">
      <div class="person">Corinne Haldwick</div>
      <div class="role">Owner</div>
    </div>
    <div class="accent-bar"></div>

    <ul class="contacts">
      <li>913-555-0147
        <svg class="icon" viewBox="0 0 24 24" aria-label="Phone">
          <path d="M6.6 10.8a15 15 0 0 0 6.6 6.6l2.2-2.2a1 1 0 0 1 1-.25 11.4 11.4 0 0 0 3.6.57 1 1 0 0 1 1 1V20a1 1 0 0 1-1 1A17 17 0 0 1 3 4a1 1 0 0 1 1-1h3.5a1 1 0 0 1 1 1c0 1.25.2 2.45.57 3.57a1 1 0 0 1-.25 1z" fill="var(--paper)"/>
        </svg>
      </li>
      <li>Rosalind Thorpe Gardens <span class="icon mark-circle"></span></li>
      <li>@RosalindThorpeGardens <span class="icon mark-square"></span></li>
      <li>RosalindThorpeGardens.example
        <svg class="icon" viewBox="0 0 24 24" aria-label="Website">
          <circle cx="12" cy="12" r="10" fill="none" stroke="var(--paper)" stroke-width="2"/>
          <ellipse cx="12" cy="12" rx="4.5" ry="10" fill="none" stroke="var(--paper)" stroke-width="1.6"/>
          <line x1="2" y1="12" x2="22" y2="12" stroke="var(--paper)" stroke-width="1.6"/>
        </svg>
      </li>
    </ul>
  </section>

</body>
</html>
```